automotive repair and collision repair shop card

our company is called K.L Motor service we are a automotive repair company
we also do government inspections. the company information is on the cards. I would like you to use my new logo and create a new card and use the information from my old card. Good Luck!!

Industry/Entity Type

Car Repair

Contact Information for Business Card

Address: #417-18842 52 Ave, Surrey, BC V5K 8R3
Phone:(604) 555-0187
fax 604 555 0193
website www.klmotorworks.example

Font styles to use
Serif
Sans Serif

Requirements
Must have
• all the information
Should not have
• the owner and there name

```html
<!DOCTYPE html>
<html lang="en">
<head>
<meta charset="UTF-8">
<title>K.L Motor service — Business Card</title>
<link rel="stylesheet" href="https://fonts.googleapis.com/css2?family=Oswald:wght@400&family=Roboto+Condensed:wght@300;400&display=swap">
<style>
  :root {
    --backdrop: #ebebeb;
    --card: #1f1e1e;
    --card-edge: #2a2929;
    --ink: #e6e6e6;
    --ink-soft: #bdbdbd;
    --bullet: #8a8a8a;
    --art-a: #2b2a2a;
    --art-b: #1f1e1e;
  }
  * { margin: 0; padding: 0; box-sizing: border-box; }
  html, body {
    width: 1200px;
    height: 800px;
    overflow: hidden;
    background: var(--backdrop);
  }
  .canvas {
    position: relative;
    width: 1200px;
    height: 800px;
    display: flex;
    align-items: center;
    justify-content: center;
    gap: 60px;
  }
  .card {
    position: relative;
    width: 520px;
    height: 297px;
    background: var(--card);
    border: 1px solid var(--card-edge);
    box-shadow: 0 6px 18px rgba(0,0,0,0.18);
    overflow: hidden;
    font-family: "Roboto Condensed", sans-serif;
    color: var(--ink);
  }

  /* Back: services + contact */
  .card-back .car-art {
    position: absolute;
    left: 20px;
    top: 30px;
    width: 270px;
    height: 170px;
    border-radius: 40px 90px 20px 20px;
    background: linear-gradient(120deg, var(--art-a), var(--art-b));
  }
  .services {
    position: absolute;
    left: 300px;
    top: 26px;
    list-style: none;
    font-size: 13px;
    font-weight: 300;
    line-height: 15px;
    color: var(--ink-soft);
  }
  .services li::before {
    content: "";
    display: inline-block;
    width: 3px;
    height: 3px;
    margin: 0 6px 3px 0;
    background: var(--bullet);
    border-radius: 50%;
  }
  .back-brand {
    position: absolute;
    left: 300px;
    top: 160px;
    display: flex;
    flex-direction: column;
  }
  .brand-name {
    font-family: "Oswald", sans-serif;
    font-weight: 400;
    color: var(--ink);
    text-transform: uppercase;
    letter-spacing: 1px;
    line-height: 1;
  }
  .back-brand .brand-name { font-size: 20px; }
  .brand-tagline {
    font-family: "Roboto Condensed", sans-serif;
    font-weight: 300;
    color: var(--ink-soft);
    margin-top: 4px;
  }
  .back-brand .brand-tagline { font-size: 10px; }
  .contact {
    position: absolute;
    left: 28px;
    bottom: 28px;
    font-style: normal;
    font-size: 13px;
    font-weight: 300;
    line-height: 16px;
    color: var(--ink-soft);
  }

  /* Front: centred brand */
  .card-front {
    display: flex;
    align-items: center;
    justify-content: center;
  }
  .front-brand {
    display: flex;
    flex-direction: column;
    align-items: center;
  }
  .front-brand .brand-name { font-size: 38px; letter-spacing: 2px; }
  .front-brand .brand-tagline { font-size: 15px; margin-top: 6px; }
</style>
</head>
<body>
<main class="canvas">
  <section class="card card-back" aria-label="Card back">
    <div class="car-art" role="img" aria-label="Faint sports car illustration"></div>
    <ul class="services">
      <li>Oil change</li>
      <li>Scheduled maintenance</li>
      <li>Body Work</li>
      <li>Paint</li>
      <li>Glass Replacement</li>
      <li>NWIC Claims</li>
      <li>Inspections</li>
      <li>Engine repair</li>
    </ul>
    <div class="back-brand">
      <span class="brand-name">K.L Motor service</span>
      <span class="brand-tagline">One Stop Repair Shop</span>
    </div>
    <address class="contact">
      #417-18842 52 Ave, Surrey, BC V5K 8R3<br>
      604 555-0187<br>
      604 555 0193<br>
      www.klmotorworks.example
    </address>
  </section>

  <section class="card card-front" aria-label="Card front">
    <div class="front-brand">
      <span class="brand-name">K.L Motor service</span>
      <span class="brand-tagline">One Stop Repair Shop</span>
    </div>
  </section>
</main>
</body>
</html>
```